Brightway Haus Inc. Business Card Design

Brightway Haus Inc. is in search of a great clean design for our business cards!

Looking to incorporate our full logo and watermark on side one (however, I am open to having the text and watermark separated within the design.)

On side two, I am looking to have contact information (Name, Position, Phone #, Email, Website (www.thebrightwayhaus.ca). Can have the logo and/or watermark as part of the design if applicable.

Please add tagline "Where Shine Counts" on either side 1 or 2. This tagline can be in a sans serif, serif or cursive font as long as it compliments overall design. Capitalization can be title or sentence case depending on how it fits within the design.

Get creative!! Looking for a clean, crisp, premium design! Looking for a glossy card finish with spot UV features when printed. Cards will also be printed with rounded corners. Standard dimensions (3.5 x 2).

Target Market(s)

B2B - primary clients are business owners or property management corporations. (residential jobs are few and far between)

Industry/Entity Type

Business

Contact Information for Business Card

- clean, crisp design
- double sided
- spot UV accents and glossy finish upon printing
- standard business card size (3.5 x 2) with rounded corners
- please see project description for requirements per side

Font styles to use
Sans Serif

Requirements
Must have
• - adequate bleeds with print ready files
• - cohesive design elements between side 1 & 2
• - spot UV elements (can be on both sides or just one, use your discretion)
• - colour pallet should match the logo file provided
• - incorporate tagline "where shine counts" (this tagline can be in a serif or sans serif font as long as it is complimentary to the overall design.
Nice to have
• - Premium elements with a clean design
Should not have
• - Please omit cartoon or whimsical like designs, think premium.
• - Colours should not stray from the pallet of the provided logo.

```html
<!DOCTYPE html>
<html lang="en">
<head>
<meta charset="utf-8">
<title>Brightway Haus Inc. – Business Card</title>
<link rel="stylesheet" href="https://fonts.googleapis.com/css2?family=Roboto:wght@400;500;700&display=swap">
<style>
  :root {
    --backdrop: #ebe7e1;
    --card-dark: #1b1c1e;
    --mark-faint: #25282a;
    --navy: #1b2452;
    --teal: #16b4b9;
    --paper: #f4f4f4;
    --white: #ffffff;
    --divider: #c9cfe0;
  }
  * { box-sizing: border-box; margin: 0; padding: 0; }
  html, body {
    width: 1200px; height: 960px; overflow: hidden;
    background: var(--backdrop);
    font-family: "Roboto", Arial, sans-serif;
  }
  .canvas { position: relative; width: 1200px; height: 960px; }

  .card {
    position: absolute; left: 320px; width: 600px; height: 342px;
    border-radius: 18px; overflow: hidden;
  }

  /* Front side */
  .card--front { top: 110px; background: var(--card-dark); }
  .front__mark {
    position: absolute; left: 200px; top: 22px; width: 200px; height: 296px;
    background: var(--mark-faint); border-radius: 6px;
  }
  .front__brand {
    position: absolute; left: 0; right: 0; top: 128px; text-align: center;
    font-weight: 700; font-size: 40px; letter-spacing: -0.5px;
    color: var(--teal); text-transform: uppercase;
  }
  .front__tagline {
    position: absolute; left: 0; right: 0; top: 193px; text-align: center;
    font-weight: 400; font-size: 15px; letter-spacing: 0.52em;
    color: var(--white);
  }

  /* Back side */
  .card--back { top: 493px; background: var(--paper); }
  .back__waves { position: absolute; inset: 0; }
  .back__brand {
    position: absolute; left: 0; right: 0; top: 72px;
    display: flex; justify-content: center; align-items: center; gap: 12px;
  }
  .back__brand-square { width: 40px; height: 40px; background: var(--teal); }
  .back__brand-name {
    font-weight: 700; font-size: 36px; letter-spacing: -0.5px;
    color: var(--navy); text-transform: uppercase;
  }

  .contact {
    position: absolute; top: 244px; left: 0; right: 0; height: 84px;
    color: var(--white);
  }
  .contact__person {
    position: absolute; right: 320px; top: 0; text-align: right;
    font-size: 14px; line-height: 19px;
  }
  .contact__name { color: var(--teal); font-weight: 700; font-size: 19px; line-height: 20px; }
  .contact__role { font-weight: 700; font-size: 15px; }
  .contact__divider {
    position: absolute; left: 301px; top: -4px; width: 1px; height: 88px;
    background: var(--divider);
  }
  .contact__lines {
    position: absolute; left: 324px; top: 0; list-style: none;
    font-size: 14px; line-height: 19px;
  }
  .contact__lines li { display: flex; align-items: center; gap: 8px; }
  .contact__icon { width: 13px; height: 13px; flex: none; }
</style>
</head>
<body>
<main class="canvas">

  <section class="card card--front" aria-label="Front of business card">
    <div class="front__mark" aria-hidden="true"></div>
    <h1 class="front__brand">Brightway Haus Inc.</h1>
    <p class="front__tagline">Where Shine Counts</p>
  </section>

  <section class="card card--back" aria-label="Back of business card">
    <svg class="back__waves" viewBox="0 0 600 342" width="600" height="342" aria-hidden="true">
      <path fill="#1b2452" d="M0,97 C40,170 110,212 230,207 C380,198 500,152 600,124 L600,342 L0,342 Z"/>
      <path fill="#ffffff" d="M0,97 C40,170 110,212 230,207 C380,198 500,152 600,124 L600,121 C500,149 380,195 230,204 C110,209 40,168 0,94 Z"/>
      <path fill="#16b4b9" d="M58,140 C110,198 170,208 240,203 C380,192 500,140 600,98 L600,120 C500,148 380,193 240,202 C170,206 105,196 58,140 Z"/>
    </svg>

    <div class="back__brand">
      <span class="back__brand-square" aria-hidden="true"></span>
      <span class="back__brand-name">Brightway Haus Inc.</span>
    </div>

    <div class="contact">
      <div class="contact__person">
        <p class="contact__name">MARA ELLISON</p>
        <p class="contact__role">CEO/FOUNDER</p>
        <p>214 Harbour Crest Way</p>
        <p>Halifax, Nova Scotia 30418</p>
      </div>
      <span class="contact__divider" aria-hidden="true"></span>
      <ul class="contact__lines">
        <li>
          <svg class="contact__icon" viewBox="0 0 16 16" aria-hidden="true"><path fill="#16b4b9" d="M3.6 1.5l2.3 2.6-1.3 1.9c.9 1.9 2.4 3.4 4.3 4.3l1.9-1.3 2.6 2.3-1.3 2.4C7 13.4 2.6 9 1.2 2.8z"/></svg>
          <span>604 512 7781</span>
        </li>
        <li>
          <svg class="contact__icon" viewBox="0 0 16 16" aria-hidden="true"><rect x="4" y="0.5" width="8" height="15" rx="1.5" fill="#16b4b9"/><rect x="5.5" y="2.5" width="5" height="9" fill="#1b2452"/></svg>
          <span>604 938 2046</span>
        </li>
        <li>
          <svg class="contact__icon" viewBox="0 0 16 16" aria-hidden="true"><rect x="4" y="1" width="8" height="4" fill="#16b4b9"/><rect x="1" y="6" width="14" height="6" rx="1" fill="#16b4b9"/><rect x="4" y="10" width="8" height="5" fill="#16b4b9" stroke="#1b2452"/></svg>
          <span>604 275 6613</span>
        </li>
        <li>
          <svg class="contact__icon" viewBox="0 0 16 16" aria-hidden="true"><rect x="1" y="3" width="14" height="10" fill="#16b4b9"/><path d="M1 3.5 L8 9 L15 3.5" fill="none" stroke="#1b2452" stroke-width="1.3"/></svg>
          <span>mara@brightwayhaus.ca</span>
        </li>
      </ul>
    </div>
  </section>

</main>
</body>
</html>
```